Local fast-growing company in the service sector

We are looking for a modern business card design, which should also appear on our letterheads

Target Market(s)

Private and industrial sectors

Contact Information for Business Card

Vorname Name
Kellberger Str. 18
73614 Lindenau
Tel.: 07146-839214-0
Name@agentur-kvtl.de

Colors
9d9d9d
919191
aaaaaa

Requirements
Must have
• The logo (file) in silver

```html
<!DOCTYPE html>
<html lang="de">
<head>
<meta charset="utf-8">
<title>KVTL Business Card</title>
<link href="https://fonts.googleapis.com/css2?family=Lato:wght@400;700;900&display=swap" rel="stylesheet">
<style>
  :root {
    --backdrop: #3a3a3a;
    --card: #f7f7f7;
    --silver-dark: #919191;
    --silver: #9d9d9d;
    --silver-light: #aaaaaa;
    --ink: #4a4a4a;
    --ink-soft: #6a6a6a;
  }
  * { margin: 0; padding: 0; box-sizing: border-box; }
  html, body {
    width: 1200px;
    height: 997px;
    overflow: hidden;
    background: var(--backdrop);
    font-family: "Lato", sans-serif;
  }
  .stage {
    width: 1200px;
    height: 997px;
    display: flex;
    align-items: center;
    justify-content: center;
  }
  .business-card {
    position: relative;
    width: 840px;
    height: 480px;
    background: var(--card);
    box-shadow: 0 10px 30px rgba(0,0,0,0.35);
  }
  .accent-rule {
    position: absolute;
    left: 48px;
    width: 4px;
    background: var(--silver-light);
  }
  .accent-rule--top { top: 0; height: 270px; }
  .accent-rule--bottom { bottom: 0; height: 46px; }
  .brand {
    position: absolute;
    top: 40px;
    right: 60px;
    display: flex;
    align-items: center;
    gap: 14px;
  }
  .brand-mark {
    width: 46px;
    height: 46px;
    background: var(--silver);
  }
  .brand-text {
    display: flex;
    flex-direction: column;
  }
  .brand-name {
    font-weight: 900;
    font-size: 44px;
    letter-spacing: 1px;
    color: var(--silver-dark);
    line-height: 1;
  }
  .brand-web {
    font-weight: 900;
    font-size: 15px;
    letter-spacing: 1px;
    color: var(--silver-dark);
    line-height: 1.2;
  }
  .contact-block {
    position: absolute;
    left: 72px;
    top: 292px;
  }
  .person-name {
    font-weight: 700;
    font-size: 19px;
    color: var(--ink);
  }
  .person-title {
    font-size: 13px;
    color: var(--ink-soft);
    margin-top: 2px;
  }
  .contact-list {
    list-style: none;
    margin-top: 16px;
  }
  .contact-item {
    display: flex;
    align-items: center;
    gap: 12px;
    font-size: 17px;
    color: var(--ink);
    line-height: 1.45;
  }
  .contact-icon {
    width: 14px;
    height: 14px;
    flex: none;
    fill: var(--silver-light);
  }
</style>
</head>
<body>
  <main class="stage">
    <article class="business-card">
      <span class="accent-rule accent-rule--top"></span>
      <span class="accent-rule accent-rule--bottom"></span>

      <header class="brand">
        <span class="brand-mark"></span>
        <span class="brand-text">
          <span class="brand-name">KVTL</span>
          <span class="brand-web">agentur-kvtl.de</span>
        </span>
      </header>

      <section class="contact-block">
        <h1 class="person-name">Lena Hartwig</h1>
        <p class="person-title">Head Customer Care Unit</p>
        <ul class="contact-list">
          <li class="contact-item">
            <svg class="contact-icon" viewBox="0 0 16 16" aria-hidden="true"><path d="M3 2h3l1.5 3.5-2 1.2a8 8 0 0 0 3.8 3.8l1.2-2L14 10v3a1.5 1.5 0 0 1-1.6 1.5A12 12 0 0 1 1.5 3.6 1.5 1.5 0 0 1 3 2z"/></svg>
            07146-839214-0
          </li>
          <li class="contact-item">
            <svg class="contact-icon" viewBox="0 0 16 16" aria-hidden="true"><path d="M1 3h14v10H1z M2 4l6 5 6-5" fill-rule="evenodd"/></svg>
            Name@agentur-kvtl.de
          </li>
          <li class="contact-item">
            <svg class="contact-icon" viewBox="0 0 16 16" aria-hidden="true"><path d="M8 1a5 5 0 0 0-5 5c0 4 5 9 5 9s5-5 5-9a5 5 0 0 0-5-5zm0 7a2 2 0 1 1 0-4 2 2 0 0 1 0 4z"/></svg>
            Kellberger Str. 18, 73614 Lindenau
          </li>
        </ul>
      </section>
    </article>
  </main>
</body>
</html>
```